real esate business card with company logo and name

we need a business card design for a real esate company

The company name is Walsh & Brand Pty Ltd, and we have our logo designed and will upload. We want classic or moden feel. Black or white background. looks more textured. Should include folowinginformations
Owen Walsh and Lucy Brand
Sales Agents & Onsite Manager
p: 07 5948 2063
F: 07 5948 2174
M:0431 857 219
3/42 Marlow Crescent, FERNLEA QLD 4213

We want this business card looks professonal. Thank you in advance.

Industry/Entity Type

Real Estate Agent

Contact Information for Business Card

Owen Walsh and Lucy Brand
Onsite Manager & Sales Agents
p: 07 5948 2063
M:0431 857 219

Font styles to use
Serif

Colors
000000
fbfbfb
333333
959595

Requirements
Must have
• company logo and name, black or white back ground

```html
<!DOCTYPE html>
<html lang="en">
<head>
<meta charset="utf-8">
<title>Walsh &amp; Brand Pty Ltd – Business Card</title>
<link rel="stylesheet" href="https://fonts.googleapis.com/css2?family=PT+Sans:wght@400;700&display=swap">
<style>
  :root {
    --ink: #000000;
    --paper: #fbfbfb;
    --charcoal: #333333;
    --silver: #959595;
    --mist: #cfcfcf;
    --stage: #e6e4e1;
  }
  html, body {
    margin: 0;
    padding: 0;
    width: 1200px;
    height: 892px;
    overflow: hidden;
    background: var(--stage);
  }
  .card {
    position: absolute;
    left: 100px;
    top: 160px;
    width: 1000px;
    height: 572px;
    border-radius: 22px;
    overflow: hidden;
    box-shadow: 0 10px 30px rgba(0,0,0,0.18);
    font-family: "PT Sans", "Helvetica Neue", Arial, sans-serif;
  }
  .card-bands {
    position: absolute;
    inset: 0;
    width: 100%;
    height: 100%;
  }
  .brand {
    position: absolute;
    left: 270px;
    top: 120px;
    display: flex;
    align-items: center;
    gap: 14px;
  }
  .brand-mark {
    width: 22px;
    height: 22px;
    background: var(--silver);
  }
  .brand-name {
    font-size: 22px;
    font-weight: 700;
    letter-spacing: 1.5px;
    text-transform: uppercase;
    color: var(--silver);
  }
  .details {
    position: absolute;
    left: 0;
    right: 0;
    top: 215px;
    text-align: center;
    color: var(--ink);
  }
  .partners {
    font-size: 44px;
    font-weight: 400;
    margin: 0;
    line-height: 1.1;
  }
  .role {
    font-size: 27px;
    margin: 4px 0 22px;
    color: var(--charcoal);
  }
  .contact {
    font-size: 24px;
    line-height: 1.32;
    margin: 0;
    color: var(--ink);
  }
  .address {
    font-size: 24px;
    line-height: 1.32;
    margin: 0;
    color: var(--ink);
  }
</style>
</head>
<body>
  <article class="card">
    <svg class="card-bands" viewBox="0 0 1000 572" aria-hidden="true">
      <defs>
        <linearGradient id="band-black" x1="0" y1="0" x2="0" y2="1">
          <stop offset="0" stop-color="#2a2a2a"/>
          <stop offset="0.5" stop-color="#111111"/>
          <stop offset="1" stop-color="#2a2a2a"/>
        </linearGradient>
        <linearGradient id="face-white" x1="0" y1="0" x2="1" y2="0">
          <stop offset="0" stop-color="#f3f3f3"/>
          <stop offset="0.5" stop-color="#fbfbfb"/>
          <stop offset="1" stop-color="#f3f3f3"/>
        </linearGradient>
      </defs>
      <rect class="band-outer" width="1000" height="572" fill="url(#band-black)"/>
      <path class="band-silver" d="M92,0 Q22,286 92,572 L908,572 Q978,286 908,0 Z" fill="#959595"/>
      <path class="band-mist" d="M106,0 Q40,286 106,572 L894,572 Q960,286 894,0 Z" fill="#cfcfcf"/>
      <path class="band-light" d="M122,0 Q60,286 122,572 L878,572 Q940,286 878,0 Z" fill="#e4e4e4"/>
      <path class="card-face" d="M134,0 Q74,286 134,572 L866,572 Q926,286 866,0 Z" fill="url(#face-white)"/>
    </svg>

    <div class="brand">
      <span class="brand-mark"></span>
      <span class="brand-name">Walsh &amp; Brand Pty Ltd</span>
    </div>

    <div class="details">
      <h1 class="partners">Owen Walsh and Lucy Brand</h1>
      <p class="role">Onsite Manager &amp; Sales Agents</p>
      <p class="contact">07 5948 2063<br>0431 857 219</p>
      <p class="address">3/42 Marlow Crescent,<br>FERNLEA QLD 4213</p>
    </div>
  </article>
</body>
</html>
```